Talvoro bonds (Surety bond broker)

We are a broker of surety bonds, we need a presentation and a flyer with fresh design. Our core values are reliable, on time and customized service. We want to transmit to our clients, they can leave on us the process of underwriting and issuing a surety bond, so they can focus on their business with no distractions.

Font styles to use
Sans Serif
Other font styles liked:

Requirements
Must have
• Visually attractive.
Main Message: Fast service issuing and underwriting surety bonds, reliable, nos surprises, we are always one step ahead, customized and personalized bonding solutions.
Nice to have
• Have short version for the flyer, and extended version for the presentation.
Should not have
• We already have a logo (attached), maintain colors

```html
<!DOCTYPE html>
<html lang="es">
<head>
<meta charset="utf-8">
<title>Talvoro Bonds — ¿Quiénes somos?</title>
<link href="https://fonts.googleapis.com/css2?family=Merriweather:wght@300;400;700&display=swap" rel="stylesheet">
<style>
  :root {
    --brand-green: #6ca844;
    --brand-black: #1f1e20;
    --text-dark: #1b1b1b;
    --bg-white: #ffffff;
    --bg-lime: #d9ea9c;
    --bg-leaf: #a9d37c;
  }
  html, body {
    margin: 0;
    padding: 0;
    overflow: hidden;
    background: var(--bg-white);
  }
  .slide {
    position: relative;
    width: 1200px;
    height: 848px;
    overflow: hidden;
    background:
      radial-gradient(ellipse 520px 420px at 1150px 120px, var(--bg-leaf) 0%, rgba(169,211,124,0) 70%),
      radial-gradient(ellipse 520px 380px at 1120px 520px, var(--bg-lime) 0%, rgba(217,234,156,0) 72%),
      radial-gradient(ellipse 600px 500px at 760px 180px, #e4f0c0 0%, rgba(228,240,192,0) 70%),
      linear-gradient(200deg, #cfe6a4 0%, #eef6dc 45%, var(--bg-white) 75%);
  }
  .slide__shapes {
    position: absolute;
    inset: 0;
  }
  .slide__title {
    position: absolute;
    left: 26px;
    top: 350px;
    width: 360px;
    margin: 0;
    font-family: "Merriweather", serif;
    font-weight: 700;
    font-size: 68px;
    line-height: 70px;
    text-align: center;
    color: var(--bg-white);
    letter-spacing: -1px;
  }
  .about {
    position: absolute;
    left: 631px;
    top: 236px;
    width: 537px;
    font-family: "Merriweather", serif;
    font-weight: 300;
    font-size: 18px;
    line-height: 24px;
    color: var(--text-dark);
  }
  .about p {
    margin: 0 0 35px;
    text-align: justify;
  }
  .brand {
    position: absolute;
    right: 32px;
    top: 772px;
    margin: 0;
    font-family: "Merriweather", serif;
    font-weight: 300;
    font-size: 30px;
    line-height: 36px;
    color: var(--text-dark);
  }
</style>
</head>
<body>
<main class="slide">
  <svg class="slide__shapes" viewBox="0 0 1200 848" width="1200" height="848" aria-hidden="true">
    <path class="shape-green-panel" fill="var(--brand-green)"
          d="M0,0 L532,0 C522,270 390,600 130,848 L0,848 Z"/>
    <path class="shape-green-stripe" fill="var(--brand-green)"
          d="M643,86 C620,330 470,640 250,848 L236,848 C450,640 610,350 643,86 Z"/>
    <path class="shape-black-swoosh" fill="var(--brand-black)"
          d="M562,0 L656,0 C612,300 460,640 180,836 C400,640 540,330 562,0 Z"/>
    <path class="shape-green-tail" fill="var(--brand-green)"
          d="M438,612 C380,700 300,780 196,848 L214,848 C310,780 390,700 438,612 Z"/>
  </svg>

  <h1 class="slide__title">¿Quiénes somos?</h1>

  <section class="about">
    <p>Talvoro Bonds, somos un grupo de jóvenes emprendedores, con amplia experiencia en el sector afianzador.</p>
    <p>Estamos convencidos de que nuestro principal diferenciador es la pasión por el servicio.</p>
    <p>Nuestra prioridad es el éxito de cada uno de nuestros clientes, nos aseguramos de que el “trámite” de fianzas deje de ser un “trámite” y se convierta en la llave del éxito para cada uno de nuestros fiados y beneficiarios.</p>
    <p>Buscamos siempre tener relaciones estrechas y de largo plazo con todos nuestros ”stakeholders”. Por lo que nos rodeamos del mejor talento en el sector para garantizar a nuestros clientes un servicio personalizado, en tiempo y confiable.</p>
  </section>

  <p class="brand">Talvoro</p>
</main>
</body>
</html>
```